Social media app sign-up flow that asks users to give personal info and connect with other apps

Design an interactive, fun, and playful sign-up flow in which you are providing information about you, your interests, and connecting with different API plug-ins such as Chatterloop, Workvine, Tunevale, etc. (using the brand palette attached).

Basic wireframe, and business requirements are also attached.

Target Market(s)

Gen Z + Millennials (ages 22-40)

Font styles to use
Sans Serif

Colors
fbed22
fbee3d
fbf289

Requirements
Must have
• Forms for users to submit their info. Follow the color palette attached.

Connect with Chatterloop, Connect with Workvine, Connect with Tunevale, Connect with Gatherpost buttons
Nice to have
• I like the way you can use cards to submit your information for each category. Interactive card design for providing your info
Should not have
• Basic outdated designs, long forms

```html
<!DOCTYPE html>
<html lang="en">
<head>
<meta charset="utf-8">
<title>Social Media App – Sign-up Flow</title>
<link href="https://fonts.googleapis.com/css2?family=Rajdhani:wght@400;500;600;700&display=swap" rel="stylesheet">
<style>
:root{
  --yellow:#fbed22;
  --yellow-soft:#fbee3d;
  --yellow-pale:#fbf289;
  --amber:#fbbd2c;
  --slate:#5b6472;
  --ink:#1d1d1d;
  --panel-head:#ececec;
  --panel-title:#545c68;
  --board:#6e6e6e;
  --line:#d9d9d9;
}
*{box-sizing:border-box;margin:0;padding:0}
html,body{width:675px;height:1200px;overflow:hidden;background:var(--board)}
body{font-family:"Rajdhani",sans-serif;color:var(--ink)}
.canvas{position:relative;width:675px;height:1200px;overflow:hidden}
.board{position:absolute;left:0;top:0;width:1372px;height:2440px;transform:scale(.49198);transform-origin:0 0}
.board-wave{position:absolute;left:0;top:0}

.screen{position:absolute;width:375px;background:#fff;overflow:hidden}
.screen-head{position:absolute;left:0;top:0;width:375px;height:130px}
.app-title{position:absolute;left:0;top:18px;width:100%;text-align:center;font-weight:700;font-size:34px;letter-spacing:.5px;color:var(--ink)}
.screen-foot{position:absolute;left:0;bottom:0;width:375px;height:120px}

.panel{position:absolute;left:17px;top:164px;width:341px;border:1px solid var(--line);border-radius:4px;background:#fff;overflow:hidden}
.panel-head{height:68px;background:var(--panel-head);text-align:center;line-height:68px;font-weight:700;font-size:34px;color:var(--panel-title);letter-spacing:.5px}
.at{position:absolute}

.field-label{left:25px;font-weight:500;font-size:19px;color:#333}
.select{left:27px;width:285px;height:55px;border:1px solid #9a9a9a;font-size:14px;color:#7a7a7a;padding-left:25px;line-height:53px}
.select::after{content:"";position:absolute;right:20px;top:24px;border-left:5px solid transparent;border-right:5px solid transparent;border-top:5px solid #444}
.note{left:27px;width:295px;font-size:14px;line-height:21px;color:#444}
.btn-continue{left:27px;width:285px;height:55px;background:linear-gradient(#fbb42a,#fdd742);color:#fff;font-weight:700;font-size:31px;text-align:center;line-height:55px;letter-spacing:.5px}
.or{left:0;width:100%;text-align:center;font-weight:700;font-size:22px;color:#222}
.btn{left:27px;width:285px;height:58px;display:flex;align-items:center;gap:14px;padding-left:34px;color:#fff;font-weight:600;font-size:20px}
.btn .mark{width:16px;height:16px;background:#fff;border-radius:3px;flex:none}
.btn .mark.round{border-radius:50%}
.btn-email{background:linear-gradient(#fbb42a,#fdd742);padding-left:34px}
.btn-chatterloop{background:linear-gradient(#2140c4,#0b1a78)}
.btn-searchly{background:linear-gradient(#f41e1e,#c10000)}
.btn-orchard{background:linear-gradient(#6d7583,#262b33)}
.btn-workvine{background:linear-gradient(#2aa3d4,#0a4d84)}
.btn-tunevale{background:linear-gradient(#5cc42c,#1c850d)}
.login-line{left:27px;font-size:16px;color:#444}
.login-line b{font-weight:700;color:#222;margin-left:6px}

.tile{width:147px;height:137px;display:flex;flex-direction:column;align-items:center;justify-content:center;gap:12px;color:#fff;font-weight:700;font-size:18px;line-height:26px;text-align:center;text-transform:uppercase}
.tile svg{width:34px;height:34px}
.tile-dark{background:linear-gradient(#1e232b,#3b4049);border:2px solid #fbb42a}
.tile-amber{background:linear-gradient(#fbb02a,#fdd24e)}
.tile-tan{background:linear-gradient(#b7985a,#d9c290)}
.tile-slate{background:linear-gradient(#3d4657,#6d7687)}
.tile-charcoal{background:linear-gradient(#2a2e35,#4b5059)}
.tile-sun{background:linear-gradient(#fbb42a,#fedc5a)}
.tile-mist{background:linear-gradient(#98a4b7,#cbd3de)}

.pick-box{left:18px;top:84px;width:306px;height:433px;background:#f3f3f3;border:1px solid #dcdcdc}
.chip{position:absolute;width:135px;height:44px;background:#fff;border:1px solid #e3e3e3;display:flex;align-items:center;gap:10px;padding-left:12px;font-weight:700;font-size:15px;line-height:14px;color:#1d1d1d}
.chip.plain{padding-left:16px}
.chip-x{position:absolute;right:-1px;top:-1px;width:24px;height:24px;background:#fbb42a;border-radius:0 0 0 16px;color:#fff;font-size:14px;font-weight:700;text-align:center;line-height:20px;padding-left:4px}
.flag{width:28px;height:16px;flex:none}
.entry{position:absolute;left:13px;top:137px;width:279px;height:77px;background:#fff;border:1px solid #e3e3e3}
.entry-typed{position:absolute;left:17px;top:12px;font-size:12px;color:#777;letter-spacing:.3px}
.entry-hint{position:absolute;left:0;top:37px;width:100%;border-top:1px solid #eee;padding:9px 17px;font-size:16px;color:#777}
.entry-hint b{color:#111;font-weight:700}
</style>
</head>
<body>
<div class="canvas">
<div class="board">

  <svg class="board-wave" width="1372" height="2440" viewBox="0 0 1372 2440" aria-hidden="true">
    <path d="M0,1470 Q686,1250 1372,1580 V2440 H0 Z" fill="var(--amber)"/>
  </svg>

  <!-- Sign-up screen, upper view -->
  <section class="screen" style="left:76px;top:90px;height:760px">
    <svg class="screen-head" viewBox="0 0 375 130" aria-hidden="true">
      <path d="M0,0 H375 V85 Q187,165 0,85 Z" fill="var(--slate)"/>
      <path d="M0,0 H375 V45 Q187,155 0,45 Z" fill="var(--yellow)"/>
    </svg>
    <h1 class="app-title">SOCIAL MEDIA APP</h1>
    <div class="panel" style="top:200px;height:600px">
      <div class="panel-head">SIGN UP</div>
      <div class="at field-label" style="top:98px">Country/Region</div>
      <div class="at select" style="top:140px">United States(+1)</div>
      <div class="at field-label" style="top:219px">Phone Number</div>
      <div class="at select" style="top:261px">United States(+1)</div>
      <div class="at note" style="top:336px">We'll call or text you to confirm your Number. Standard message and data rates apply.</div>
      <div class="at btn-continue" style="top:398px">CONTINUE</div>
      <div class="at or" style="top:482px">(OR)</div>
      <div class="at btn btn-email" style="top:532px">
        <svg width="18" height="14" viewBox="0 0 18 14" aria-hidden="true"><rect width="18" height="14" rx="1" fill="#fff"/><path d="M1,1 L9,8 L17,1" stroke="#fbc43a" stroke-width="1.6" fill="none"/></svg>
        Continue with Email</div>
    </div>
  </section>

  <!-- Sign-up screen, full -->
  <section class="screen" style="left:519px;top:85px;height:1218px">
    <svg class="screen-head" viewBox="0 0 375 130" aria-hidden="true">
      <path d="M0,0 H375 V85 Q187,165 0,85 Z" fill="var(--slate)"/>
      <path d="M0,0 H375 V45 Q187,155 0,45 Z" fill="var(--yellow)"/>
    </svg>
    <h1 class="app-title">SOCIAL MEDIA APP</h1>
    <div class="panel" style="height:896px">
      <div class="panel-head">SIGN UP</div>
      <div class="at field-label" style="top:98px">Country/Region</div>
      <div class="at select" style="top:140px">United States(+1)</div>
      <div class="at field-label" style="top:219px">Phone Number</div>
      <div class="at select" style="top:261px">United States(+1)</div>
      <div class="at note" style="top:336px">We'll call or text you to confirm your Number. Standard message and data rates apply.</div>
      <div class="at btn-continue" style="top:398px">CONTINUE</div>
      <div class="at or" style="top:482px">(OR)</div>
      <div class="at btn btn-email" style="top:532px">
        <svg width="18" height="14" viewBox="0 0 18 14" aria-hidden="true"><rect width="18" height="14" rx="1" fill="#fff"/><path d="M1,1 L9,8 L17,1" stroke="#fbc43a" stroke-width="1.6" fill="none"/></svg>
        Continue with Email</div>
      <div class="at btn btn-chatterloop" style="top:599px"><span class="mark"></span>Continue with Chatterloop</div>
      <div class="at btn btn-searchly" style="top:667px"><span class="mark"></span>Continue with Searchly</div>
      <div class="at btn btn-orchard" style="top:734px"><span class="mark round"></span>Continue with Orchard</div>
      <div class="at login-line" style="top:824px">Already have an account?<b>LOGIN</b></div>
    </div>
    <svg class="screen-foot" viewBox="0 0 375 120" aria-hidden="true">
      <path d="M0,120 V60 Q187,-46 375,60 V120 Z" fill="var(--slate)"/>
      <path d="M0,120 V82 Q187,-34 375,82 V120 Z" fill="var(--yellow)"/>
      <g stroke="#1d1d1d" stroke-width="3" fill="none" stroke-linecap="round">
        <path d="M90,68 H110 M90,76 H110 M90,84 H110"/>
        <rect x="181" y="67" width="18" height="18" rx="3"/>
        <path d="M284,66 L274,76 L284,86"/>
      </g>
    </svg>
  </section>

  <!-- Tell me about you -->
  <section class="screen" style="left:924px;top:85px;height:1017px">
    <svg class="screen-head" viewBox="0 0 375 130" aria-hidden="true">
      <path d="M0,0 H375 V85 Q187,165 0,85 Z" fill="var(--slate)"/>
      <path d="M0,0 H375 V45 Q187,155 0,45 Z" fill="var(--yellow)"/>
    </svg>
    <h1 class="app-title">SOCIAL MEDIA APP</h1>
    <div class="panel" style="height:703px">
      <div class="panel-head">TELL ME ABOUT YOU</div>
      <div class="at tile tile-dark" style="left:18px;top:84px">
        <svg viewBox="0 0 24 24" aria-hidden="true"><path d="M12,2 C7.6,2 5,5.2 5,9 C5,14 12,22 12,22 C12,22 19,14 19,9 C19,5.2 16.4,2 12,2 Z" fill="#fff"/><circle cx="12" cy="9" r="3" fill="#2a2e35"/></svg>
        <span>Places I've<br>lived</span></div>
      <div class="at tile tile-amber" style="left:178px;top:84px">
        <svg viewBox="0 0 24 24" aria-hidden="true" fill="#fff"><path d="M12,2 L22,7 H2 Z"/><rect x="3" y="8" width="18" height="2"/><rect x="5" y="11" width="2" height="7"/><rect x="9" y="11" width="2" height="7"/><rect x="13" y="11" width="2" height="7"/><rect x="17" y="11" width="2" height="7"/><rect x="2" y="19" width="20" height="3"/></svg>
        <span>Schools I've<br>attended</span></div>
      <div class="at tile tile-tan" style="left:18px;top:235px">
        <svg viewBox="0 0 24 24" aria-hidden="true"><rect x="2" y="3" width="20" height="14" rx="1.5" fill="#fff"/><rect x="4" y="5" width="16" height="10" fill="#c8ad74"/><rect x="10" y="17" width="4" height="3" fill="#fff"/><rect x="7" y="20" width="10" height="2" fill="#fff"/></svg>
        <span>Places I've<br>worked</span></div>
      <div class="at tile tile-slate" style="left:178px;top:235px">
        <svg viewBox="0 0 24 24" aria-hidden="true" fill="#fff"><circle cx="12" cy="7" r="5"/><path d="M3,22 C3,15 21,15 21,22 Z"/></svg>
        <span>People I<br>know</span></div>
      <div class="at tile tile-charcoal" style="left:18px;top:385px">
        <svg viewBox="0 0 24 24" aria-hidden="true" fill="none" stroke="#fff" stroke-width="2"><rect x="3" y="5" width="18" height="16" rx="1"/><path d="M3,10 H21 M8,2 V7 M16,2 V7"/></svg>
        <span>Events I've<br>attended</span></div>
      <div class="at tile tile-amber" style="left:178px;top:385px">
        <svg viewBox="0 0 24 24" aria-hidden="true" fill="none" stroke="#fff" stroke-width="1.8"><rect x="3" y="5" width="18" height="16" rx="1"/><path d="M3,10 H21 M8,2 V7 M16,2 V7 M3,14 H21 M3,17.5 H21 M7.5,10 V21 M12,10 V21 M16.5,10 V21"/></svg>
        <span>Events I'm<br>attending</span></div>
      <div class="at tile tile-sun" style="left:18px;top:536px">
        <svg viewBox="0 0 24 24" aria-hidden="true" fill="#fff"><path d="M9,4 L21,1 V17 H19 V6 L11,8 V19 H9 Z"/><circle cx="6.5" cy="19" r="3.5"/><circle cx="17" cy="17" r="3.5"/></svg>
        <span>Music I<br>love</span></div>
      <div class="at tile tile-mist" style="left:178px;top:536px">
        <svg viewBox="0 0 24 24" aria-hidden="true" fill="#fff"><circle cx="12" cy="7" r="3.5"/><circle cx="5" cy="8" r="2.5"/><circle cx="19" cy="8" r="2.5"/><path d="M6,20 C6,12 18,12 18,20 Z"/><path d="M0,18 C0,12 6,11 7,13 L5,18 Z"/><path d="M24,18 C24,12 18,11 17,13 L19,18 Z"/></svg>
        <span>Teams I<br>love</span></div>
    </div>
    <svg class="screen-foot" viewBox="0 0 375 120" aria-hidden="true">
      <path d="M0,120 V60 Q187,-46 375,60 V120 Z" fill="var(--slate)"/>
      <path d="M0,120 V82 Q187,-34 375,82 V120 Z" fill="var(--yellow)"/>
      <g stroke="#1d1d1d" stroke-width="3" fill="none" stroke-linecap="round">
        <path d="M90,68 H110 M90,76 H110 M90,84 H110"/>
        <rect x="181" y="67" width="18" height="18" rx="3"/>
        <path d="M284,66 L274,76 L284,86"/>
      </g>
    </svg>
  </section>

  <!-- Places I've lived -->
  <section class="screen" style="left:74px;top:926px;height:1017px">
    <svg class="screen-head" viewBox="0 0 375 130" aria-hidden="true">
      <path d="M0,0 H375 V85 Q187,165 0,85 Z" fill="var(--slate)"/>
      <path d="M0,0 H375 V45 Q187,155 0,45 Z" fill="var(--yellow)"/>
    </svg>
    <h1 class="app-title">SOCIAL MEDIA APP</h1>
    <div class="panel" style="height:703px">
      <div class="panel-head">PLACES I'VE LIVED</div>
      <div class="at pick-box">
        <div class="chip" style="left:13px;top:21px">
          <svg class="flag" viewBox="0 0 28 16" aria-hidden="true"><rect width="28" height="16" fill="#fff"/><rect y="4" width="28" height="2" fill="#7fc4ec"/><rect y="10" width="28" height="2" fill="#7fc4ec"/><g fill="#e02020"><circle cx="8" cy="8" r="1"/><circle cx="12" cy="8" r="1"/><circle cx="16" cy="8" r="1"/><circle cx="20" cy="8" r="1"/></g></svg>
          CHICAGO<span class="chip-x">×</span></div>
        <div class="chip" style="left:157px;top:21px">
          <svg class="flag" viewBox="0 0 28 16" aria-hidden="true"><rect width="28" height="16" fill="#c8102e"/><rect x="11" y="5" width="6" height="6" fill="#2a3a8a"/></svg>
          MADRID<span class="chip-x">×</span></div>
        <div class="chip" style="left:13px;top:79px">
          <svg class="flag" viewBox="0 0 28 16" aria-hidden="true"><rect width="9.3" height="16" fill="#1f3fb0"/><rect x="9.3" width="9.4" height="16" fill="#fff"/><rect x="18.7" width="9.3" height="16" fill="#e3262b"/></svg>
          PARIS<span class="chip-x">×</span></div>
        <div class="chip" style="left:157px;top:79px">
          <svg class="flag" viewBox="0 0 28 16" aria-hidden="true"><rect width="28" height="16" fill="#fff"/><path d="M2,1 L26,15 M26,1 L2,15" stroke="#2a4fb5" stroke-width="3"/><circle cx="14" cy="8" r="3" fill="#e02020"/></svg>
          <span style="text-align:center">RIO DE<br>JANIERO</span><span class="chip-x">×</span></div>
        <div class="entry">
          <div class="entry-typed">LONDO |</div>
          <div class="entry-hint"><b>London</b>,United Kingdom</div>
        </div>
      </div>
      <div class="at btn btn-chatterloop" style="top:545px"><span class="mark"></span>Connect with Chatterloop</div>
      <div class="at btn btn-workvine" style="top:613px"><span class="mark"></span>Connect with Workvine</div>
    </div>
    <svg class="screen-foot" viewBox="0 0 375 120" aria-hidden="true">
      <path d="M0,120 V60 Q187,-46 375,60 V120 Z" fill="var(--slate)"/>
      <path d="M0,120 V82 Q187,-34 375,82 V120 Z" fill="var(--yellow)"/>
      <g stroke="#1d1d1d" stroke-width="3" fill="none" stroke-linecap="round">
        <path d="M90,68 H110 M90,76 H110 M90,84 H110"/>
        <rect x="181" y="67" width="18" height="18" rx="3"/>
        <path d="M284,66 L274,76 L284,86"/>
      </g>
    </svg>
  </section>

  <!-- Music I love -->
  <section class="screen" style="left:519px;top:1339px;height:1017px">
    <svg class="screen-head" viewBox="0 0 375 130" aria-hidden="true">
      <path d="M0,0 H375 V85 Q187,165 0,85 Z" fill="var(--slate)"/>
      <path d="M0,0 H375 V45 Q187,155 0,45 Z" fill="var(--yellow)"/>
    </svg>
    <h1 class="app-title">SOCIAL MEDIA APP</h1>
    <div class="panel" style="height:703px">
      <div class="panel-head">MUSIC I LOVE</div>
      <div class="at pick-box">
        <div class="chip plain" style="left:13px;top:21px">NEON HARBOR<span class="chip-x">×</span></div>
        <div class="chip plain" style="left:157px;top:21px">ZEPHYRA MOSS<span class="chip-x">×</span></div>
        <div class="chip plain" style="left:13px;top:79px">60 VOLT<span class="chip-x">×</span></div>
        <div class="chip plain" style="left:157px;top:79px">RAY CALLOWAY<span class="chip-x">×</span></div>
        <div class="entry">
          <div class="entry-typed">BRINLEY SHO |</div>
          <div class="entry-hint"><b>Brinley Shore</b></div>
        </div>
      </div>
      <div class="at btn btn-chatterloop" style="top:545px"><span class="mark"></span>Connect with Chatterloop</div>
      <div class="at btn btn-tunevale" style="top:613px"><span class="mark round"></span>Connect with Tunevale</div>
    </div>
    <svg class="screen-foot" viewBox="0 0 375 120" aria-hidden="true">
      <path d="M0,120 V60 Q187,-46 375,60 V120 Z" fill="var(--slate)"/>
      <path d="M0,120 V82 Q187,-34 375,82 V120 Z" fill="var(--yellow)"/>
      <g stroke="#1d1d1d" stroke-width="3" fill="none" stroke-linecap="round">
        <path d="M90,68 H110 M90,76 H110 M90,84 H110"/>
        <rect x="181" y="67" width="18" height="18" rx="3"/>
        <path d="M284,66 L274,76 L284,86"/>
      </g>
    </svg>
  </section>

</div>
</div>
</body>
</html>
```